Ward Compass Business Card Design*

We need a business card design for our company Ward Compass. Our company is specialized in providing online consulting services regarding medical institutions, hospitals and doctors. We work with patients worldwide looking to choose between healthcare providers. We have a website you may use as a reference, where we list doctors and clinics worldwide. So we target Medical providers as well as patients worldwide.
Target Market(s)
Medical Providers and patients around the world
Industry/Entity Type
Medical
Contact Information for Business Card
Salwa Kettani
CEO
+90 612 348 2175
info@wardcompass.example
www.wardcompass.example
14 Annakhil 7 H.R.B. Rabat, Morocco
Requirements
Must have
- Company logo/name on one full side, personal info and smaller logo and company name on the other side.
Nice to have
- Smart and elegant design

```html
<!DOCTYPE html>
<html lang="en">
<head>
<meta charset="utf-8">
<title>Ward Compass Business Card</title>
<link rel="stylesheet" href="https://fonts.googleapis.com/css2?family=Montserrat:wght@300;400;600;700&display=swap">
<style>
  :root {
    --backdrop: #e9e6e1;
    --card-light: #f7f7f9;
    --brand-blue: #2c4b7e;
    --ink-gray: #6d6f73;
    --soft-gray: #9a9ca0;
    --rule-gray: #c9cbd0;
    --watermark: #e3e5ec;
    --white: #ffffff;
  }
  * { margin: 0; padding: 0; box-sizing: border-box; }
  html, body {
    width: 900px; height: 1200px; overflow: hidden;
    background: var(--backdrop);
    font-family: "Montserrat", Arial, sans-serif;
  }
  .canvas { position: relative; width: 900px; height: 1200px; }

  .card {
    position: absolute; left: 66px; width: 768px;
    box-shadow: 0 6px 18px rgba(0,0,0,0.18);
    overflow: hidden;
  }
  .card-front { top: 105px; height: 510px; background: var(--card-light); }
  .card-back  { top: 645px; height: 465px; background: var(--brand-blue); }

  .brand { display: flex; align-items: center; gap: 14px; position: absolute; }
  .brand-dot { border-radius: 50%; flex: none; }
  .brand-name { font-weight: 600; text-transform: uppercase; letter-spacing: 0.5px; white-space: nowrap; }

  .card-front .brand { left: 60px; top: 118px; }
  .card-front .brand-dot { width: 46px; height: 46px; background: var(--brand-blue); }
  .card-front .brand-name { font-size: 30px; color: var(--brand-blue); }

  .watermark { position: absolute; right: 70px; top: 55px; }

  .person { position: absolute; left: 60px; top: 225px; }
  .person-name { font-size: 25px; letter-spacing: 0.5px; text-transform: uppercase; color: var(--ink-gray); font-weight: 400; }
  .person-name .first { color: var(--brand-blue); font-weight: 700; }
  .person-role { font-size: 15px; color: var(--soft-gray); margin-top: 4px; }
  .person-rule { width: 260px; height: 1px; background: var(--rule-gray); margin-top: 8px; }

  .contacts { position: absolute; left: 60px; top: 340px; list-style: none; }
  .contacts li { display: flex; align-items: center; gap: 14px; font-size: 15px; color: var(--ink-gray); height: 32px; }
  .contact-icon { width: 20px; height: 20px; flex: none; }

  .address { position: absolute; left: 470px; top: 350px; font-size: 15px; line-height: 30px; color: var(--ink-gray); font-style: normal; }

  .card-back .brand { left: 50%; top: 180px; transform: translateX(-50%); gap: 20px; }
  .card-back .brand-dot { width: 80px; height: 80px; background: var(--white); }
  .card-back .brand-name { font-size: 44px; color: var(--white); }

  .website { position: absolute; left: 0; right: 0; top: 408px; text-align: center; font-size: 15px; letter-spacing: 3px; color: var(--white); opacity: 0.9; }
</style>
</head>
<body>
<main class="canvas">
  <section class="card card-front" aria-label="Business card front">
    <svg class="watermark" width="290" height="290" viewBox="0 0 290 290" aria-hidden="true">
      <circle cx="145" cy="145" r="130" fill="none" stroke="var(--watermark)" stroke-width="26"/>
    </svg>
    <div class="brand">
      <span class="brand-dot"></span>
      <span class="brand-name">Ward Compass</span>
    </div>
    <div class="person">
      <h1 class="person-name"><span class="first">Salwa</span> Kettani</h1>
      <p class="person-role">CEO</p>
      <div class="person-rule"></div>
    </div>
    <ul class="contacts">
      <li>
        <svg class="contact-icon" viewBox="0 0 20 20" aria-hidden="true">
          <circle cx="10" cy="10" r="10" fill="var(--brand-blue)"/>
          <path d="M7 5.5l1.6 0 .8 2.3-1.1.8a6 6 0 0 0 3.1 3.1l.8-1.1 2.3.8v1.6c0 .6-.5 1-1.1 1A8.4 8.4 0 0 1 6 6.6c0-.6.4-1.1 1-1.1z" fill="var(--white)"/>
        </svg>
        +90 612 348 2175
      </li>
      <li>
        <svg class="contact-icon" viewBox="0 0 20 20" aria-hidden="true">
          <circle cx="10" cy="10" r="10" fill="var(--brand-blue)"/>
          <rect x="5" y="6.5" width="10" height="7" rx="1" fill="var(--white)"/>
          <path d="M5.3 7l4.7 3.6L14.7 7" fill="none" stroke="var(--brand-blue)" stroke-width="1"/>
        </svg>
        info@wardcompass.example
      </li>
    </ul>
    <address class="address">14 Annakhil 7 H.R.B.<br>Rabat, Morocco</address>
  </section>

  <section class="card card-back" aria-label="Business card back">
    <div class="brand">
      <span class="brand-dot"></span>
      <span class="brand-name">Ward Compass</span>
    </div>
    <p class="website">www.wardcompass.example</p>
  </section>
</main>
</body>
</html>
```